sydney wedding photography business needs a business card design

we need a business card design for a sydney based wedding photography and videography business. our business name is :golden hour studio and film. our target clients are 24-35 yrs female. our style is candid, organic, natural, dynamic. we are a team of young photographers and videographers, and help brides to create memories that they will cherish for the rest of their lives. the logo will be provided. we want an elegant design that reflects our style, and also want to give a great impression to our clients that we are one of the best studios in sydney and our brand means quality and premium service.

Target Market(s)

bride to be, 24-35 years old, living in sydney and surrunding areas

Industry/Entity Type

Wedding Photography

Contact Information for Business Card

address: 57 tarrant street, glenmore nsw 2047
mobile: 0431872259
phone: (02) 9163 2408
info@tidewillowstudio.net.au
www.tidewillowstudio.net.au
facebook:tidewillowweddings
instagram:tidewillowweddings

Font styles to use
Serif
Sans Serif

Requirements
Nice to have
• maybe add my slogan"memories beyond eternity" if the layout looks good
Should not have
• no black color, not good idea for wedding biz card

```html
<!DOCTYPE html>
<html lang="en">
<head>
<meta charset="utf-8">
<title>Golden Hour Studio and Film — Business Card</title>
<link rel="stylesheet" href="https://fonts.googleapis.com/css2?family=Josefin+Sans:wght@400&family=Pinyon+Script&family=Arimo:wght@400&display=swap">
<style>
  :root {
    --backdrop: #574638;
    --card-front-top: #4a3222;
    --card-front-bottom: #3a2718;
    --gold: #dcaa2a;
    --gold-top: #ddab0f;
    --gold-mid: #cf9a12;
    --gold-bottom: #a8761a;
    --ink: #17110a;
    --frame-gold: #d6a020;
  }
  * { margin: 0; padding: 0; box-sizing: border-box; }
  html, body { width: 1200px; height: 987px; overflow: hidden; }
  body {
    background: var(--backdrop);
    position: relative;
    font-family: "Arimo", Arial, sans-serif;
  }
  .card {
    position: absolute;
    left: 293px;
    width: 615px;
    height: 351px;
    overflow: hidden;
  }
  .card--front {
    top: 127px;
    background: linear-gradient(180deg, var(--card-front-top) 0%, var(--card-front-bottom) 100%);
  }
  .card--back {
    top: 509px;
    background: linear-gradient(180deg, var(--gold-top) 0%, var(--gold-mid) 45%, var(--gold-bottom) 100%);
    color: var(--ink);
  }
  .frame { position: absolute; inset: 0; width: 615px; height: 351px; }

  .brand-name {
    position: absolute;
    left: 0; right: 0;
    top: 156px;
    text-align: center;
    font-family: "Josefin Sans", Arial, sans-serif;
    font-weight: 400;
    font-size: 29px;
    letter-spacing: 2px;
    color: var(--gold);
  }

  .contact-block {
    position: absolute;
    left: 0; right: 0;
    top: 76px;
    text-align: center;
  }
  .person-name {
    font-family: "Pinyon Script", cursive;
    font-size: 42px;
    line-height: 50px;
  }
  .person-role {
    font-size: 15px;
    line-height: 18px;
    letter-spacing: 0.3px;
    margin-bottom: 20px;
  }
  .contact-line {
    font-size: 16px;
    line-height: 22px;
  }
  .social {
    margin-top: 19px;
    display: flex;
    justify-content: center;
    align-items: center;
    gap: 6px;
    font-size: 16px;
    line-height: 22px;
  }
  .social-dot {
    width: 16px; height: 16px;
    border-radius: 50%;
    background: var(--ink);
    display: inline-block;
  }
</style>
</head>
<body>
  <section class="card card--front" aria-label="Card front">
    <svg class="frame" viewBox="0 0 615 351" fill="none" stroke="var(--frame-gold)" stroke-width="2">
      <path d="M23 88 V22 H90"/>
      <path d="M525 22 H592 V88"/>
      <path d="M23 263 V329 H90"/>
      <path d="M525 329 H592 V263"/>
    </svg>
    <p class="brand-name">Golden Hour Studio and Film</p>
  </section>

  <section class="card card--back" aria-label="Card back">
    <svg class="frame" viewBox="0 0 615 351" fill="none" stroke="var(--ink)" stroke-width="2">
      <path d="M23 88 V22 H90"/>
      <path d="M525 22 H592 V88"/>
      <path d="M23 263 V329 H90"/>
      <path d="M525 329 H592 V263"/>
    </svg>
    <div class="contact-block">
      <p class="person-name">Clara Whitmore</p>
      <p class="person-role">PHOTOGRAPHER</p>
      <p class="contact-line">P. (02) 9163 2408 M. (04) 3187 2259</p>
      <p class="contact-line">E. info@tidewillowstudio.net.au W. tidewillowstudio.net.au</p>
      <p class="contact-line">57 tarrant street, glenmore nsw 2047</p>
      <p class="social"><span class="social-dot"></span>TIDEWILLOWWEDDINGS</p>
    </div>
  </section>
</body>
</html>
```